Christmas Banner for frontpage of website

New online scarf store just opened needs a Christmas Banner stating Free Delivery (UK only). Also if it could incorporate guaranteed Christmas delivery if ordered before 18th (might be too wordy though?) I would really like it to bring some colour to the page. The page is currently black and white with a pink accent and is very simple which is why I would like something modern and elegant, simple but with some colour. It is a shopify store I understand the banner size should be 950px by 290px the website is www.tolvarenshop.co.uk

Target Market(s)

Ladies

Industry/Entity Type

Store

Requirements
Should not have
• Not to look tacky.

```html
<!DOCTYPE html>
<html lang="en">
<head>
<meta charset="utf-8">
<title>Christmas Banner</title>
<link rel="stylesheet" href="https://fonts.googleapis.com/css2?family=Damion&family=Dancing+Script:wght@600&family=Patrick+Hand&display=swap">
<style>
  :root {
    --bg: #dfe3e8;
    --bg-shade: #cfd4da;
    --ink: #3a3b3d;
    --red: #d42a1f;
    --badge: #c8201a;
    --white: #ffffff;
    --gold: #e8b10f;
    --antler-tone: #b9bdc3;
    --antler-edge: #a9adb4;
    --santa: #d8322a;
    --holly: #2f8a3a;
    --gift: #5aa83a;
    --blue-orn: #2f7fc4;
    --star: #f2c21b;
    --tree: #3b9a3f;
    --bauble: #e23a86;
    --flake: #e8504a;
    --snowman: #f3f3f1;
  }
  html, body {
    margin: 0;
    padding: 0;
    overflow: hidden;
  }
  .banner {
    position: relative;
    width: 1200px;
    height: 366px;
    overflow: hidden;
    background:
      radial-gradient(ellipse 260px 120px at 120px 40px, var(--bg-shade), transparent 70%),
      radial-gradient(ellipse 300px 140px at 1100px 60px, var(--bg-shade), transparent 70%),
      radial-gradient(ellipse 340px 110px at 600px 360px, var(--bg-shade), transparent 70%),
      var(--bg);
    font-family: "Damion", cursive;
  }
  .strings {
    position: absolute;
    inset: 0;
  }
  .ornament {
    position: absolute;
    border-radius: 8px;
  }
  .ornament--santa   { left: 54px;   top: 142px; width: 56px; height: 82px; background: var(--santa); }
  .ornament--holly   { left: 98px;   top: 98px;  width: 34px; height: 26px; background: var(--holly); border-radius: 50%; }
  .ornament--gift    { left: 128px;  top: 136px; width: 42px; height: 40px; background: var(--gift); }
  .ornament--blue    { left: 37px;   top: 254px; width: 16px; height: 22px; background: var(--blue-orn); border-radius: 4px; }
  .ornament--star    { left: 1014px; top: 106px; width: 36px; height: 36px; background: var(--star); border-radius: 50%; }
  .ornament--tree    { left: 1069px; top: 106px; width: 30px; height: 52px; background: var(--tree); border-radius: 14px 14px 4px 4px; }
  .ornament--bauble  { left: 1126px; top: 136px; width: 36px; height: 36px; background: var(--bauble); border-radius: 50%; }
  .ornament--flake   { left: 1043px; top: 170px; width: 28px; height: 28px; background: var(--flake); border-radius: 50%; }
  .ornament--snowman { left: 1092px; top: 204px; width: 54px; height: 68px; background: var(--snowman); border-radius: 26px; }

  .antlers {
    position: absolute;
    left: 490px;
    top: 26px;
    width: 240px;
    height: 104px;
    background: linear-gradient(180deg, var(--antler-tone), var(--antler-edge));
    opacity: 0.45;
    border-radius: 70px 70px 40px 40px;
  }
  .badge {
    position: absolute;
    left: 555px;
    top: 34px;
    width: 104px;
    height: 104px;
  }
  .badge svg { display: block; }
  .badge__text {
    position: absolute;
    inset: 0;
    display: flex;
    flex-direction: column;
    align-items: center;
    justify-content: center;
    color: var(--white);
    font-family: "Patrick Hand", cursive;
    text-align: center;
    line-height: 1;
  }
  .badge__main { font-size: 19px; }
  .badge__note { font-size: 13px; margin-top: 5px; }

  .headline {
    position: absolute;
    left: 0;
    right: 0;
    top: 146px;
    margin: 0;
    text-align: center;
    color: var(--ink);
    font-weight: 400;
  }
  .headline__line { display: block; line-height: 68px; }
  .headline__line--merry { font-size: 94px; }
  .headline__line--christmas { font-size: 88px; }

  .tagline {
    position: absolute;
    left: 0;
    right: 0;
    top: 308px;
    margin: 0;
    text-align: center;
    color: var(--red);
    font-family: "Dancing Script", cursive;
    font-weight: 600;
    font-size: 25px;
    line-height: 32px;
  }
</style>
</head>
<body>
<main class="banner">
  <svg class="strings" width="1200" height="366" aria-hidden="true">
    <g stroke="var(--gold)" stroke-width="3" stroke-linecap="round" stroke-dasharray="0.1 6" fill="none">
      <line x1="45" y1="0" x2="45" y2="254"/>
      <line x1="82" y1="0" x2="82" y2="142"/>
      <line x1="115" y1="0" x2="115" y2="98"/>
      <line x1="149" y1="0" x2="149" y2="136"/>
      <line x1="1032" y1="0" x2="1032" y2="106"/>
      <line x1="1057" y1="0" x2="1057" y2="170"/>
      <line x1="1084" y1="0" x2="1084" y2="106"/>
      <line x1="1119" y1="0" x2="1119" y2="204"/>
      <line x1="1144" y1="0" x2="1144" y2="136"/>
    </g>
  </svg>

  <div class="ornament ornament--santa" role="img" aria-label="Hanging Santa Claus ornament"></div>
  <div class="ornament ornament--holly" role="img" aria-label="Hanging holly sprig ornament"></div>
  <div class="ornament ornament--gift" role="img" aria-label="Hanging green gift box ornament"></div>
  <div class="ornament ornament--blue" role="img" aria-label="Small hanging blue ornament"></div>
  <div class="ornament ornament--star" role="img" aria-label="Hanging gold star ornament"></div>
  <div class="ornament ornament--tree" role="img" aria-label="Hanging Christmas tree ornament"></div>
  <div class="ornament ornament--bauble" role="img" aria-label="Hanging pink snowflake bauble"></div>
  <div class="ornament ornament--flake" role="img" aria-label="Hanging red snowflake ornament"></div>
  <div class="ornament ornament--snowman" role="img" aria-label="Hanging snowman ornament"></div>

  <div class="antlers" role="img" aria-label="Dark reindeer antlers illustration"></div>

  <div class="badge">
    <svg width="104" height="104" viewBox="0 0 112 112" aria-hidden="true">
      <polygon fill="var(--badge)" points="56,2 63,10 73,5 77,15 88,14 88,25 99,28 96,38 105,45 98,53 105,61 96,68 99,78 88,81 88,92 77,91 73,101 63,96 56,104 49,96 39,101 35,91 24,92 24,81 13,78 16,68 7,61 14,53 7,45 16,38 13,28 24,25 24,14 35,15 39,5 49,10"/>
      <circle cx="56" cy="53" r="42" fill="none" stroke="var(--white)" stroke-width="1" stroke-dasharray="2 3" opacity="0.5"/>
    </svg>
    <div class="badge__text">
      <span class="badge__main">Free<br>Delivery</span>
      <span class="badge__note">(UK only)</span>
    </div>
  </div>

  <h1 class="headline">
    <span class="headline__line headline__line--merry">Merry</span>
    <span class="headline__line headline__line--christmas">Christmas</span>
  </h1>

  <p class="tagline">guaranteed Christmas delivery if ordered before 18th</p>
</main>
</body>
</html>
```